NEW Modern Sleek Business Card for VR Language Startup

Our startup is using VR to lead the next wave of world language education. We need a two-sided business card that introduces the larger organization (Brightloom Language Inc) and our contact info on one side and shows the product, Glimwoorld, on the other side.

Side 1 (contact info)= Brightloom Logo and Contact info (name, title, phone, email)

Side 2 (product)= Glimworld logo, text, and website
Text= Culturally Immersive Language Learning Games
Website= www.glimworld-play.com

Target Market(s)

Education, Technology

Contact Information for Business Card

Contact info will be updated upon approval of the design. For now, put this as a placeholder.

Perry Dunmore
Founder & CEO
pdunmore@quillpost-mail.net
(555)-014-2286

Font styles to use
Other font styles liked:
• Gibson and Century Gothic are the brand fonts

Requirements
Nice to have
• I would love to see cohesion between the design and colors of the two logos. I have attached a few business card designs that I like, so you can get a feel for my preferred style.

```html
<!DOCTYPE html>
<html lang="en">
<head>
<meta charset="utf-8">
<title>Glimworld &amp; Brightloom Business Cards</title>
<link href="https://fonts.googleapis.com/css2?family=Roboto:ital,wght@0,400;0,500;0,700;1,500&display=swap" rel="stylesheet">
<style>
  :root {
    --backdrop: #e3e4e7;
    --card-dark: #222222;
    --card-light: #ffffff;
    --ink-light: #ffffff;
    --ink-dark: #1d1d1d;
    --brand-red: #f2344a;
    --brand-violet: #8a4df0;
    --brand-blue: #3aa6f5;
    --brand-cyan: #3fd4f2;
    --rule-blue: #4a6cf0;
  }
  * { box-sizing: border-box; margin: 0; padding: 0; }
  html, body {
    width: 1200px; height: 800px; overflow: hidden;
    background: var(--backdrop);
  }
  .sheet {
    position: relative; width: 1200px; height: 800px;
    display: flex; align-items: center; justify-content: center; gap: 50px;
  }
  .card {
    position: relative; width: 540px; height: 309px; overflow: hidden;
    box-shadow: 0 6px 18px rgba(0,0,0,0.18);
  }

  /* Product side */
  .card--product { background: var(--card-dark); color: var(--ink-light); }
  .product-mark {
    position: absolute; left: 0; right: 0; top: 92px;
    display: flex; align-items: center; justify-content: center; gap: 14px;
  }
  .product-mark__dot {
    width: 34px; height: 34px; border-radius: 50%;
    background: linear-gradient(160deg, var(--brand-cyan), var(--brand-violet));
  }
  .product-mark__name {
    font-family: "Roboto", sans-serif; font-weight: 500; font-size: 46px;
    letter-spacing: 0.5px; color: var(--ink-light);
  }
  .product-tagline {
    position: absolute; left: 0; right: 0; top: 178px; text-align: center;
    font-family: "Roboto", sans-serif; font-style: italic; font-weight: 500;
    font-size: 16px; color: var(--ink-light);
  }
  .product-web {
    position: absolute; left: 0; right: 0; top: 214px;
    display: flex; align-items: center; justify-content: center; gap: 12px;
    font-family: "Roboto", sans-serif; font-size: 15px; color: var(--ink-light);
  }
  .product-web__rule { display: block; }

  /* Contact side */
  .card--contact { background: var(--card-light); }
  .contact-band {
    position: absolute; left: 0; right: 0; top: 112px; bottom: 0;
    background: linear-gradient(170deg, var(--brand-red) 0%, var(--brand-violet) 60%, var(--brand-blue) 100%);
  }
  .contact-info {
    position: absolute; left: 44px; top: 140px; color: var(--ink-light);
    font-family: "Roboto", sans-serif;
  }
  .contact-info__name { font-weight: 700; font-size: 21px; }
  .contact-info__title { font-weight: 500; font-size: 14px; margin-top: 1px; }
  .contact-info__list { list-style: none; margin-top: 10px; font-size: 12.5px; }
  .contact-info__list li { display: flex; align-items: center; gap: 7px; margin-top: 4px; }
  .contact-info__icon { width: 12px; height: 12px; fill: var(--ink-light); }
  .org-mark {
    position: absolute; right: 40px; top: 38px;
    display: flex; align-items: center; gap: 10px;
  }
  .org-mark__dot {
    width: 26px; height: 26px; border-radius: 50%;
    background: linear-gradient(160deg, var(--brand-red), var(--brand-violet));
  }
  .org-mark__name {
    font-family: "Roboto", sans-serif; font-weight: 700; font-size: 28px;
    letter-spacing: 2px; color: var(--ink-dark);
  }
</style>
</head>
<body>
<main class="sheet">

  <section class="card card--product" aria-label="Product side">
    <div class="product-mark">
      <span class="product-mark__dot"></span>
      <span class="product-mark__name">Glimworld</span>
    </div>
    <p class="product-tagline">Culturally Immersive Language Learning Games</p>
    <div class="product-web">
      <svg class="product-web__rule" width="110" height="10" viewBox="0 0 110 10" aria-hidden="true">
        <defs><linearGradient id="rule-left" gradientUnits="userSpaceOnUse" x1="0" y1="0" x2="100" y2="0"><stop offset="0" stop-color="#4a6cf0" stop-opacity="0"/><stop offset="1" stop-color="#4a6cf0"/></linearGradient></defs>
        <line x1="0" y1="5" x2="100" y2="5" stroke="url(#rule-left)" stroke-width="1.5"/>
        <circle cx="104" cy="5" r="3.5" fill="none" stroke="#4a6cf0" stroke-width="1.5"/>
      </svg>
      <span>www.glimworld-play.com</span>
      <svg class="product-web__rule" width="110" height="10" viewBox="0 0 110 10" aria-hidden="true">
        <defs><linearGradient id="rule-right" gradientUnits="userSpaceOnUse" x1="10" y1="0" x2="110" y2="0"><stop offset="0" stop-color="#4a6cf0"/><stop offset="1" stop-color="#4a6cf0" stop-opacity="0"/></linearGradient></defs>
        <circle cx="6" cy="5" r="3.5" fill="none" stroke="#4a6cf0" stroke-width="1.5"/>
        <line x1="10" y1="5" x2="110" y2="5" stroke="url(#rule-right)" stroke-width="1.5"/>
      </svg>
    </div>
  </section>

  <section class="card card--contact" aria-label="Contact side">
    <div class="contact-band" role="img" aria-label="Decorative colour band in red, violet and blue"></div>
    <div class="org-mark">
      <span class="org-mark__dot"></span>
      <span class="org-mark__name">Brightloom</span>
    </div>
    <div class="contact-info">
      <p class="contact-info__name">Perry Dunmore</p>
      <p class="contact-info__title">Founder &amp; CEO</p>
      <ul class="contact-info__list">
        <li>
          <svg class="contact-info__icon" viewBox="0 0 24 24" aria-hidden="true"><path d="M6.6 10.8c1.4 2.8 3.8 5.1 6.6 6.6l2.2-2.2c.3-.3.7-.4 1-.2 1.1.4 2.3.6 3.6.6.6 0 1 .4 1 1V20c0 .6-.4 1-1 1C10.6 21 3 13.4 3 4c0-.6.4-1 1-1h3.5c.6 0 1 .4 1 1 0 1.3.2 2.5.6 3.6.1.3 0 .7-.2 1z"/></svg>
          <span>(555)-014-2286</span>
        </li>
        <li>
          <svg class="contact-info__icon" viewBox="0 0 24 24" aria-hidden="true"><path d="M2 5h20v14H2z M2 5l10 8 10-8" fill="none" stroke="#ffffff" stroke-width="2"/></svg>
          <span>pdunmore@quillpost-mail.net</span>
        </li>
      </ul>
    </div>
  </section>

</main>
</body>
</html>
```